Business Card Design For Marketing Agnecy LVP

Need business card design for marketing agency.

Doug Fenwick
President, CEO
1-555-302-4196
doug@boldpromoperksgroup.example
www.BoldPromoPerksGroup.example

Back Side:
Boost Sales Using Rewards, Incentives & Giveaways
Get A Free Sample Package

Target Market(s)

B2B

Industry/Entity Type

Marketing

Contact Information for Business Card

Doug Fenwick
President, CEO
1-555-302-4196

Back Side:
Get A Free Sample Package

Please note that my current url is OLD DESIGN. I am working on new design and want the business card to match color themes at least on new site. Here is the demo link for new site so you can see the colors I use, etc.

http://layoutcratehub.example/kq/doug/lvp_final/index.html

Requirements
Must have
• Please note that my current url is OLD DESIGN. I am working on new design and want the business card to match color themes at least on new site. Here is the demo link for new site so you can see the colors I use, etc.

Nice to have

Should not have

```html
<!DOCTYPE html>
<html lang="en">
<head>
<meta charset="utf-8">
<title>LVP Business Card</title>
<link rel="stylesheet" href="https://fonts.googleapis.com/css2?family=Montserrat:wght@600;700;800&family=Open+Sans:wght@400;500&family=Arimo:wght@400&display=swap">
<style>
  :root {
    --brand-blue: #1078c2;
    --band-grey: #58595b;
    --card-white: #ffffff;
    --page-bg: #e6e8eb;
    --ink-light: #ffffff;
  }
  * { box-sizing: border-box; margin: 0; padding: 0; }
  html, body { width: 1200px; height: 1000px; overflow: hidden; }
  body {
    background: var(--page-bg);
    position: relative;
    font-family: "Open Sans", Arial, sans-serif;
  }
  .card {
    position: absolute;
    left: 240px;
    width: 720px;
    height: 400px;
    border-radius: 22px;
    overflow: hidden;
    box-shadow: 0 10px 30px rgba(0,0,0,0.18);
  }
  /* Back side */
  .card-back { top: 60px; background: var(--brand-blue); }
  .brand-name {
    font-family: "Montserrat", Arial, sans-serif;
    font-weight: 800;
    letter-spacing: 4px;
    line-height: 1;
  }
  .card-back .brand-name {
    position: absolute;
    left: 0; right: 0; top: 110px;
    text-align: center;
    font-size: 120px;
    color: var(--ink-light);
  }
  .tagline {
    position: absolute;
    left: 0; right: 0; bottom: 38px;
    text-align: center;
    color: var(--ink-light);
    font-size: 17px;
    letter-spacing: 0.6px;
  }
  .tagline .dot { margin: 0 8px; }

  /* Front side */
  .card-front { top: 540px; background: var(--brand-blue); }
  .card-front .shape { position: absolute; inset: 0; }
  .card-front .brand-name {
    position: absolute;
    left: 20px; width: 290px; top: 145px;
    text-align: center;
    font-size: 92px;
    color: var(--brand-blue);
  }
  .person {
    position: absolute;
    left: 420px; top: 100px;
    color: var(--ink-light);
  }
  .person-name {
    font-family: "Montserrat", Arial, sans-serif;
    font-weight: 700;
    font-size: 24px;
    letter-spacing: 0.8px;
    text-transform: uppercase;
  }
  .person-title {
    font-family: "Arimo", Arial, sans-serif;
    font-size: 18px;
    margin-top: 2px;
  }
  .divider {
    width: 150px;
    height: 2px;
    background: var(--ink-light);
    margin-top: 18px;
  }
  .contacts {
    position: absolute;
    left: 405px; top: 225px;
    list-style: none;
    color: var(--ink-light);
    font-family: "Arimo", Arial, sans-serif;
    font-size: 16px;
  }
  .contacts li {
    display: flex;
    align-items: center;
    gap: 12px;
    height: 30px;
    white-space: nowrap;
  }
  .contacts svg { width: 18px; height: 18px; flex: none; }
</style>
</head>
<body>

<section class="card card-back" aria-label="Card back">
  <div class="brand-name">LVP</div>
  <p class="tagline">Boost Sales Using Rewards<span class="dot">•</span>Incentives &amp; Giveaways<span class="dot">•</span>Get A Free Sample Package</p>
</section>

<section class="card card-front" aria-label="Card front">
  <svg class="shape" viewBox="0 0 720 400" preserveAspectRatio="none" aria-hidden="true">
    <path d="M0 0 H350 C405 150 370 320 225 400 H0 Z" fill="var(--band-grey)"/>
    <path d="M0 0 H332 C387 150 347 320 192 400 H0 Z" fill="var(--card-white)"/>
  </svg>

  <div class="brand-name">LVP</div>

  <div class="person">
    <h1 class="person-name">Doug Fenwick</h1>
    <p class="person-title">President, CEO</p>
    <div class="divider"></div>
  </div>

  <ul class="contacts">
    <li>
      <svg viewBox="0 0 18 18" aria-hidden="true"><rect width="18" height="18" rx="3" fill="#fff"/><path d="M5 3.5l2 .2 1 3-1.3 1c.8 1.5 1.8 2.5 3.3 3.3l1-1.3 3 1 .2 2c-.3 1-1.2 1.6-2.2 1.5C7.8 13.8 4.2 10.2 3.8 5.9 3.7 4.8 4.2 3.8 5 3.5z" fill="var(--brand-blue)"/></svg>
      <span>1-555-302-4196</span>
    </li>
    <li>
      <svg viewBox="0 0 18 18" aria-hidden="true"><rect width="18" height="18" rx="3" fill="#fff"/><rect x="3" y="5" width="12" height="8.5" fill="none" stroke="var(--brand-blue)" stroke-width="1.4"/><path d="M3 5l6 5 6-5" fill="none" stroke="var(--brand-blue)" stroke-width="1.4"/></svg>
      <span>doug@boldpromoperksgroup.example</span>
    </li>
    <li>
      <svg viewBox="0 0 18 18" aria-hidden="true"><rect width="18" height="18" rx="3" fill="#fff"/><circle cx="9" cy="9" r="5.5" fill="none" stroke="var(--brand-blue)" stroke-width="1.4"/><path d="M3.5 9h11M9 3.5c-2.5 3-2.5 8 0 11M9 3.5c2.5 3 2.5 8 0 11" fill="none" stroke="var(--brand-blue)" stroke-width="1.1"/></svg>
      <span>www.BoldPromoPerksGroup.example</span>
    </li>
  </ul>
</section>

</body>
</html>
```